Varnel Corporate Website for technological company

We need a modern website to promote our product and services.
You can found the actually website at the address: www.varnel-example.ch

We are a new company for B2B market. We would like do show our high precision and innovation capability.

we need a section were is possible to easily upload "news" and documents for our customers.

Target Market(s)

B2B services in the industry market

Industry/Entity Type

It Company

Coding

Coded - Design and coding required

Number of Pages Required

5+ page

Font styles to use
Other font styles liked:
• We accept propositions

Requirements
Must have
• Easy to maintain
• Presentation of the Varnel company
• Presentation of Varnel services and products
• The customer can download our ducumentation
Nice to have
• Sexy and modern

```html
<!DOCTYPE html>
<html lang="en">
<head>
<meta charset="utf-8">
<title>Varnel Sagl – Mechanics and Electronic Services</title>
<link rel="stylesheet" href="https://fonts.googleapis.com/css2?family=Montserrat:wght@400;500;600;700;800&family=Open+Sans:wght@400;600&family=Raleway:wght@400;500;600&display=swap">
<style>
:root{
  --olive:#a89d55;
  --olive-card:#9d9249;
  --olive-foot:#b5a962;
  --olive-bar:#8e8443;
  --ink:#222;
  --muted:#8a8a8a;
  --cream:#f0ead0;
  --white:#fff;
}
*{box-sizing:border-box;margin:0;padding:0}
html,body{width:1200px;height:2469px;overflow:hidden;background:var(--white)}
body{position:relative;font-family:"Open Sans",Arial,sans-serif;color:var(--ink)}
.abs{position:absolute}

/* header */
.site-header{left:0;top:0;width:1200px;height:97px;background:var(--white)}
.brand{left:140px;top:30px;display:flex;align-items:center;gap:12px}
.brand-mark{width:30px;height:30px;background:var(--olive)}
.brand-name{font-family:"Montserrat",sans-serif;font-weight:800;font-size:31px;color:#1b1b1b;letter-spacing:1px}
.main-nav{left:484px;top:0;height:97px;display:flex;gap:0}
.main-nav a{display:block;height:97px;line-height:100px;padding:0 19px;font-family:"Montserrat",sans-serif;font-size:13.5px;font-weight:500;color:#333;text-decoration:none;position:relative}
.main-nav a.active{color:var(--olive)}
.main-nav a.active::after{content:"";position:absolute;left:10px;right:10px;bottom:0;height:4px;background:#111}

/* hero */
.hero{left:0;top:97px;width:1200px;height:496px;background:linear-gradient(100deg,#5a5a58 0%,#3d3d3c 35%,#a49c8c 58%,#2a2a2a 75%,#111 100%)}
.hero-title{left:140px;top:185px;font-family:"Montserrat",sans-serif;font-weight:600;font-size:41px;line-height:48px;color:var(--white);letter-spacing:.5px}
.hero-dots{left:140px;top:394px;display:flex;gap:4px}
.hero-dots span{width:17px;height:17px;border-radius:50%;background:var(--white)}
.hero-dots span.off{background:transparent;border:2px solid var(--white)}

/* services */
.services-band{left:0;top:593px;width:1200px;height:332px;background:var(--olive)}
.section-rule{display:flex;align-items:center;justify-content:center;gap:26px;width:1200px;left:0}
.section-rule i{display:block;width:60px;height:1px;background:#d6cfa0}
.section-rule h2{font-family:"Montserrat",sans-serif;font-weight:600;font-size:23px;color:var(--white);letter-spacing:.5px}
.service-card{top:668px;width:236px;height:306px;background:var(--olive-card);border-radius:12px;text-align:center;color:var(--white);box-shadow:0 3px 6px rgba(0,0,0,.08)}
.service-card svg{margin-top:38px}
.service-card h3{font-family:"Montserrat",sans-serif;font-weight:500;font-size:17px;line-height:22px;margin-top:10px;min-height:22px}
.service-card p{font-size:11.5px;line-height:19px;color:var(--cream);padding:0 18px;margin-top:8px}
.btn-outline{display:inline-block;border:1.5px solid var(--white);color:var(--white);font-family:"Montserrat",sans-serif;font-size:10.5px;padding:7px 20px;text-decoration:none}
.service-card .btn-outline{position:absolute;left:68px;top:227px;width:100px;padding:7px 0}

/* about */
.about-title{left:160px;top:1058px;font-family:"Raleway",sans-serif;font-weight:500;font-size:27px;color:#111}
.about-text{left:155px;top:1104px;width:515px;font-size:13.5px;line-height:28px;color:var(--muted)}
.about-text p+p{margin-top:6px}
.btn-read{left:155px;top:1294px;width:137px;height:38px;border:2px solid var(--olive);color:var(--olive);font-family:"Montserrat",sans-serif;font-size:12px;display:flex;align-items:center;justify-content:center}
.about-art{left:708px;top:1004px;width:332px;height:425px;background:linear-gradient(180deg,#fbfbfb 0%,#f4eee9 60%,#e8c8b4 100%)}

/* products */
.products{left:0;top:1429px;width:1200px;height:411px;background:radial-gradient(ellipse at 50% 60%,#fafafa 0%,#e4e4e4 60%,#cfcfcf 100%)}
.products-title{left:0;top:1478px;width:1200px;text-align:center;font-family:"Montserrat",sans-serif;font-size:24px;color:#444}
.product-card{top:1527px;width:292px;height:267px;background:var(--white);box-shadow:0 2px 5px rgba(0,0,0,.15)}
.product-photo{height:160px}
.product-card h3{font-family:"Montserrat",sans-serif;font-weight:400;font-size:16px;color:#222;margin:22px 0 0 24px}
.product-card p{font-size:11.5px;line-height:17px;color:var(--muted);margin:4px 24px 0}

/* news */
.news-title{left:143px;top:1880px;font-family:"Montserrat",sans-serif;font-weight:500;font-size:23px;color:var(--olive)}
.news-item{top:1932px;width:265px}
.news-item h3{font-family:"Open Sans",sans-serif;font-weight:400;font-size:18px;color:#111}
.news-item p{font-size:12.5px;line-height:19px;color:var(--muted);margin-top:6px}
.news-item time{display:block;font-size:13.5px;color:#222;margin-top:12px}

/* footer */
.site-footer{left:0;top:2151px;width:1200px;height:262px;background:var(--olive-foot);color:var(--white)}
.foot-col{top:2196px}
.foot-col h4{font-family:"Montserrat",sans-serif;font-weight:500;font-size:15px;margin-bottom:16px}
.foot-col ul{list-style:none;font-size:12.5px;line-height:24px}
.tweet{display:flex;gap:10px;font-size:10.5px;line-height:16px;margin-bottom:12px;width:190px}
.tweet .tick{flex:none;width:15px;height:15px;background:var(--white);border-radius:2px;margin-top:3px}
.tweet em{font-style:normal;color:#f2cf55}
.tweet small{display:block;margin-top:6px;font-size:10px}
.contact-line{display:flex;gap:10px;font-size:11.5px;line-height:18px;margin-bottom:12px;width:200px}
.social li{display:flex;align-items:center;gap:10px;margin-bottom:9px;font-size:12.5px}
.social li span{width:24px;height:24px;border:1.5px solid var(--white);border-radius:50%}
.bottom-bar{left:0;top:2413px;width:1200px;height:56px;background:var(--olive-bar);color:#e6dfb8;font-size:10.5px;display:flex;align-items:center;justify-content:center}
</style>
</head>
<body>

<header class="site-header abs">
  <div class="brand abs"><span class="brand-mark"></span><span class="brand-name">VARNEL Sagl</span></div>
  <nav class="main-nav abs">
    <a class="active" href="#">HOME</a><a href="#">SERVICES</a><a href="#">PRODUCTS</a><a href="#">EXAMPLES</a><a href="#">DOWNLOAD</a><a href="#">CONTACT</a>
  </nav>
</header>

<section class="hero abs" role="img" aria-label="Photograph of a precision measuring rig with microscope optics and a ring light"></section>
<h1 class="hero-title abs">MECHANICS AND<br>ELECTRONIC SERVICES</h1>
<div class="hero-dots abs"><span class="off"></span><span></span><span></span><span></span></div>

<section class="services-band abs"></section>
<div class="section-rule abs" style="top:619px"><i></i><h2>OUR SERVICES</h2><i></i></div>

<article class="service-card abs" style="left:122px">
  <svg width="60" height="60" viewBox="0 0 60 60" fill="none" stroke="#fff" stroke-width="3"><rect x="12" y="12" width="36" height="36" rx="3"/><rect x="20" y="20" width="20" height="20"/><path d="M20 4v8M30 4v8M40 4v8M20 48v8M30 48v8M40 48v8M4 20h8M4 30h8M4 40h8M48 20h8M48 30h8M48 40h8"/></svg>
  <h3>Electronics</h3>
  <p>Praesent elementum elit at tellus nec ultricies sit amet porttitor mattis enim in massa libero interd</p>
  <a class="btn-outline" href="#">CLICK HERE</a>
</article>
<article class="service-card abs" style="left:364px">
  <svg width="60" height="60" viewBox="0 0 60 60" fill="none" stroke="#fff" stroke-width="2"><path d="M6 18L18 6h36v36L42 54H6z"/><path d="M6 18h36v36M42 18L54 6"/><path d="M16 28h16v16H16z"/></svg>
  <h3>Simulation &amp;<br>Modelling</h3>
  <p>Praesent elementum elit at tellus nec ultricies sit amet porttitor</p>
  <a class="btn-outline" href="#">CLICK HERE</a>
</article>
<article class="service-card abs" style="left:604px">
  <svg width="60" height="60" viewBox="0 0 60 60" fill="none" stroke="#fff" stroke-width="2.5"><circle cx="30" cy="30" r="18"/><circle cx="30" cy="30" r="9"/><circle cx="30" cy="30" r="3"/><path d="M30 4v8M30 48v8M4 30h8M48 30h8M11.6 11.6l5.7 5.7M42.7 42.7l5.7 5.7M11.6 48.4l5.7-5.7M42.7 17.3l5.7-5.7"/></svg>
  <h3>Mechanics</h3>
  <p>Praesent elementum elit at tellus nec ultricies sit amet porttitor mattis enim in massa libero interd</p>
  <a class="btn-outline" href="#">CLICK HERE</a>
</article>
<article class="service-card abs" style="left:844px">
  <svg width="60" height="60" viewBox="0 0 60 60" fill="none" stroke="#fff" stroke-width="2"><circle cx="24" cy="24" r="18"/><circle cx="24" cy="24" r="5"/><circle cx="24" cy="24" r="11"/><circle cx="42" cy="42" r="9"/><circle cx="42" cy="42" r="3"/><path d="M42 29v4M42 51v4M29 42h4M51 42h4M33 33l3 3M48 48l3 3M33 51l3-3M48 36l3-3"/></svg>
  <h3>Software</h3>
  <p>Praesent elementum elit at tellus nec ultricies sit amet porttitor mattis enim in massa libero interd</p>
  <a class="btn-outline" href="#">CLICK HERE</a>
</article>

<h2 class="about-title abs">ABOUT OUR COMPANY</h2>
<div class="about-text abs">
  <p>The ever-increasing complexity in modern systems, the search for reliability and performance and the continuous desire to reduce production costs and dimensions of the products require a rigorous integration between the electronic units, software and mechanical systems.</p>
  <p>VARNEL Ltd. designs systems in which electronics, software and mechanics are perfectly integrated to achieve uncompromising performance.</p>
</div>
<a class="btn-read abs" href="#">READ MORE</a>
<div class="about-art abs" role="img" aria-label="Illustration of a hand sketching a glowing light bulb"></div>

<section class="products abs"></section>
<h2 class="products-title abs">OUR PRODUCTS</h2>
<article class="product-card abs" style="left:142px">
  <div class="product-photo" role="img" aria-label="Photograph of a CNC milling head machining metal parts" style="background:linear-gradient(135deg,#8c9096,#4d5258 60%,#c9ccd0)"></div>
  <h3>Product Tittle here</h3>
  <p>Praesent elementum elit at tellus nec ultricies sit amet porttitor mattis enim</p>
</article>
<article class="product-card abs" style="left:452px">
  <div class="product-photo" role="img" aria-label="Photograph of linear actuators on a blue surface" style="background:linear-gradient(135deg,#2f8fdc,#1e6fc0 50%,#3a3a3e)"></div>
  <h3>Product Tittle here</h3>
  <p>Praesent elementum elit at tellus nec ultricies sit amet porttitor mattis enim</p>
</article>
<article class="product-card abs" style="left:760px">
  <div class="product-photo" role="img" aria-label="Photograph of a gloved hand holding a copper-wound motor stator" style="background:radial-gradient(circle at 50% 55%,#6a4a34,#b8907a 55%,#e9ddd3)"></div>
  <h3>Product Tittle here</h3>
  <p>Praesent elementum elit at tellus nec ultricies sit amet porttitor mattis enim</p>
</article>

<h2 class="news-title abs">LATEST NEWS</h2>
<article class="news-item abs" style="left:145px">
  <h3>Mauris vel lacus vitae felis</h3>
  <p>The Varnel team will be present at the stand A16 of Technova exhibition in Bern, between 6 and 8 september 2016</p>
  <time>10/06/2016</time>
</article>
<article class="news-item abs" style="left:469px">
  <h3>Vestibulum volutpat</h3>
  <p>dui aliquet felis at cursus magna nisl nec elit Praesent elementum elit at tellus nec ultricies sit amet porttitor mattis</p>
  <time>10/06/2016</time>
</article>
<article class="news-item abs" style="left:802px">
  <h3>Etiam est nunc venenatis</h3>
  <p>dui aliquet felis at cursus magna nisl nec lit Praesent elementum elit at tellus nec ultricies sit amet porttitor mattis</p>
  <time>10/06/2016</time>
</article>

<footer class="site-footer abs"></footer>
<div class="foot-col abs" style="left:153px">
  <h4>INFORMATION</h4>
  <ul><li>About Us</li><li>Our Products</li><li>Our Services</li><li>Blogs</li><li>Contact Us</li></ul>
</div>
<div class="foot-col abs" style="left:403px">
  <h4>LATEST TWEET`S</h4>
  <div class="tweet"><span class="tick"></span><div><em>company name</em> sends warm regards. Cum sociis natoque penatibus et<small>1 day ago</small></div></div>
  <div class="tweet"><span class="tick"></span><div><em>company name</em> sends warm regards. Cum sociis natoque penatibus et<small>1 day ago</small></div></div>
</div>
<div class="foot-col abs" style="left:672px">
  <h4>CONTACT US</h4>
  <div class="contact-line"><svg width="14" height="18" viewBox="0 0 14 18" fill="none" stroke="#fff" stroke-width="1.5"><path d="M7 17s6-6 6-10A6 6 0 0 0 1 7c0 4 6 10 6 10z"/><circle cx="7" cy="7" r="2"/></svg><span>18 Lindenweg Suite 4 Talbach, 6900 Office 091.555.0143</span></div>
  <div class="contact-line"><svg width="16" height="16" viewBox="0 0 16 16" fill="none" stroke="#fff" stroke-width="1.5"><path d="M3 1h3l1.5 4-2 1.5a9 9 0 0 0 4 4L11 8.5l4 1.5v3a2 2 0 0 1-2 2A13 13 0 0 1 1 3a2 2 0 0 1 2-2z"/></svg><span>Phone:+41 91 555 0187</span></div>
  <div class="contact-line"><svg width="16" height="12" viewBox="0 0 16 12" fill="none" stroke="#fff" stroke-width="1.5"><rect x="1" y="1" width="14" height="10"/><path d="M1 1l7 6 7-6"/></svg><span>info@varnel-example.ch</span></div>
</div>
<div class="foot-col abs" style="left:961px">
  <h4>FOLLOW US</h4>
  <ul class="social"><li><span></span>Friendspace</li><li><span></span>Chirper</li><li><span></span>Circles+</li><li><span></span>Clipstream</li></ul>
</div>
<div class="bottom-bar abs">© 2016 Company Name All right reserved&nbsp; Term of Use</div>

</body>
</html>
```